Wexmoor Climate Business Card Design

Design new, 2 sides, business cards for a residential and light commercial heating, air conditioning contractor.

Target Market(s)

Homeowners, small businesses

Industry/Entity Type

Business

Contact Information for Business Card

Dominic Westerhall
Phone - 862-415-2736
Email
Address - PO box 518
Brightwater NJ 07912
Website - www.HarborBreezeLLC.example

Requirements
Must have
• logo, company colors, standard size with no die cut, so I can use nova stamp

```html
<!DOCTYPE html>
<html lang="en">
<head>
<meta charset="utf-8">
<title>Wexmoor Climate Business Card</title>
<link rel="stylesheet" href="https://fonts.googleapis.com/css2?family=Libre+Baskerville:wght@400;700&family=Arimo:wght@400&display=swap">
<style>
  :root {
    --ink: #1c1c1c;
    --paper: #ffffff;
    --paper-shade: #ececec;
    --muted: #555555;
    --stage: #e4e2de;
    --light-text: #f2f2f2;
  }
  * { margin: 0; padding: 0; box-sizing: border-box; }
  html, body { width: 1200px; height: 843px; overflow: hidden; }
  body { background: var(--stage); position: relative; }
  .card {
    position: absolute;
    width: 540px;
    height: 309px;
    top: 267px;
    overflow: hidden;
    box-shadow: 0 6px 18px rgba(0,0,0,0.25);
  }
  .card--back { left: 40px; background: var(--ink); color: var(--light-text); }
  .card--front { left: 620px; background: linear-gradient(180deg, var(--paper) 0%, var(--paper-shade) 60%); }

  .brand-name {
    font-family: "Libre Baskerville", serif;
    font-weight: 700;
    letter-spacing: 1px;
    white-space: nowrap;
  }
  .card--back .brand-name {
    position: absolute; left: 0; right: 0; top: 110px;
    text-align: center; font-size: 34px; color: var(--light-text);
  }
  .tagline {
    position: absolute; left: 0; right: 0; top: 190px;
    text-align: center;
    font-family: "Libre Baskerville", serif;
    font-size: 12px; letter-spacing: 1px; color: var(--light-text);
  }

  .card--front .brand-name {
    position: absolute; left: 40px; top: 40px;
    font-size: 26px; color: var(--ink);
  }
  .wave { position: absolute; inset: 0; width: 540px; height: 309px; }
  .person { position: absolute; right: 36px; top: 70px; text-align: right; }
  .person-name {
    font-family: "Libre Baskerville", serif;
    font-size: 20px; color: var(--ink); white-space: nowrap;
  }
  .person-title {
    font-family: "Libre Baskerville", serif;
    font-size: 12px; color: var(--muted); margin-top: 2px;
  }
  .contact {
    position: absolute; left: 40px; right: 90px; top: 214px;
    text-align: right;
    font-family: "Arimo", sans-serif;
    font-size: 12.5px; line-height: 20px; color: var(--light-text);
    white-space: nowrap;
  }
</style>
</head>
<body>
  <section class="card card--back" aria-label="Card back">
    <div class="brand-name">Wexmoor Climate</div>
    <p class="tagline">Residential &amp; Light Commercial Heating &amp; Cooling</p>
  </section>

  <section class="card card--front" aria-label="Card front">
    <svg class="wave" viewBox="0 0 540 309" aria-hidden="true">
      <defs>
        <linearGradient id="swoosh-fade" x1="0" x2="1" y1="0" y2="0">
          <stop offset="0" stop-color="#bdbdbd"/>
          <stop offset="0.5" stop-color="#6f6f6f"/>
          <stop offset="1" stop-color="#cfcfcf"/>
        </linearGradient>
      </defs>
      <path d="M0 108 C150 76 340 128 540 196 L540 309 L0 309 Z" fill="url(#swoosh-fade)"/>
      <path d="M0 120 C150 88 340 140 540 210 L540 309 L0 309 Z" fill="#1c1c1c"/>
    </svg>
    <div class="brand-name">Wexmoor Climate</div>
    <div class="person">
      <div class="person-name">Dominic Westerhall</div>
      <div class="person-title">CEO/Founder</div>
    </div>
    <div class="contact">
      <p>[p] (862) 415-2736 &nbsp;[c] (862) 415-2790</p>
      <p>[e] dominic@wexmoorclimate.example [w] www.WexmoorClimateLLC.example</p>
      <p>[a] PO box 518, Brightwater NJ 07912</p>
    </div>
  </section>
</body>
</html>
```